Buch-/E-Book-Cover
Tolle Designerin. Tolles Ergebnis. Das beste war die reibungslose Kommunikation.
Zielgruppe
Wir verkaufen Trainings und vermitteln über unser Buch ein erstes vertieftes Wissen zum Thema Vermögensaufbau.
Aufgabenstellung
Es soll schlicht und schön sein, Angelehnt an Smart mom slow mom, bzw. an Plane klug und bleibe frei von Gideon Farrow.
Wir benötigen die AI, etc Dateien und die fertigen Dateien für Bucholo.de Lesquill sowie Bucholo.de Books (ehemals Printvelle) mit fertigem Cover.
Vorgaben von Bucholo.de über die Homepage. Anbei ein Beispiel (wegen Bucholo.de Buchnummer etc) Abstände, Buchrücken etc.
Buch ca. 150 Seiten
https://www.bucholo-beispiel.de/Gaertner-sein-trotzdem-Freude-kleinen/dp/7302958163 Front und Backcover kann man sich da ansehen.
Der Buchtitel ist 'Baue Mauern und bleibe still' - - Lassen Sie uns freundschaftlich in entspannter Atmosphäre über Immobilien sprechen (der nebentitel so klein wie bei Smart Mom - Slow Mom)
Rücktitel: Bitte zuerst Platzhalter.
Ich bitte um 5x8 inch, also wie DIN A 5, wir nehmen cremefarbenes Papier denke ich. Die Seitenzahl kann ich auf die Seite noch nicht sagen, wir haben aber 75 Din A4 Seiten, sprich nach Formatierung eher 160-165 Din A5. WErde ich Ihnen final nach dem Gewinn sagen.
Versuchen Sie mich mal aus dem einen Bild raus zu schneiden, und dass dann mit einem Layer über das cover zu legen.
2-3 Versionen wäre gut, mit 2-3 Bildern. Buchrücken ein kleines Bild von mir.
Seite vom Buch: Titel nochmal.

```html
<!DOCTYPE html>
<html lang="de">
<head>
<meta charset="utf-8">
<title>Baue Mauern und bleibe still – Cover-Varianten</title>
<link href="https://fonts.googleapis.com/css2?family=Lato:wght@400;700;900&display=swap" rel="stylesheet">
<style>
  :root {
    --page: #ffffff;
    --night: #1f1330;
    --gold: #f7bd22;
    --white: #ffffff;
    --band-violet: rgba(70, 52, 104, 0.92);
    --ink-violet: #2a1840;
  }
  * { box-sizing: border-box; margin: 0; padding: 0; }
  html, body {
    width: 1200px; height: 5000px; overflow: hidden;
    background: var(--page);
    font-family: "Lato", sans-serif;
  }
  .cover {
    position: absolute; left: 274px; width: 720px; height: 1150px;
    overflow: hidden; background: var(--night); color: var(--white);
  }
  .cover--one { top: 392px; }
  .cover--two { top: 1922px; }
  .cover--three { top: 3452px; }

  .backdrop { position: absolute; inset: 0; width: 100%; height: 100%; }

  .portrait {
    position: absolute;
    background: linear-gradient(180deg, rgba(60,45,40,0) 0%, rgba(70,54,44,0.55) 12%, #45362d 30%, #3a2d26 65%, #2c221d 100%);
    opacity: 0.9;
  }
  .cover--one .portrait { left: 300px; top: 20px; width: 400px; height: 1130px; }
  .cover--two .portrait,
  .cover--three .portrait { left: 200px; top: 70px; width: 460px; height: 1080px; }

  .author { position: absolute; left: 64px; font-size: 26px; line-height: 1.3; }
  .author strong { font-weight: 900; }
  .author span { font-weight: 400; }
  .cover--one .author { top: 52px; }
  .cover--two .author,
  .cover--three .author { top: 36px; left: 66px; font-size: 27px; }

  .title { position: absolute; left: 12px; right: 0; text-align: center; font-weight: 900; }
  .title__line { display: block; font-size: 110px; line-height: 96px; letter-spacing: -1px; }
  .title__line--gold { color: var(--gold); }
  .title__line--white { color: var(--white); }
  .title__joiner { display: block; font-size: 38px; line-height: 46px; font-weight: 900; }
  .cover--one .title { top: 420px; }
  .cover--two .title,
  .cover--three .title { top: 488px; }

  .series-band {
    position: absolute; text-align: center;
    font-size: 34px; font-weight: 700; line-height: 56px; letter-spacing: 0.3px;
  }
  .series-band--gold { left: 66px; width: 604px; top: 892px; background: var(--gold); color: var(--ink-violet); }
  .series-band--violet { background: var(--band-violet); color: var(--white); }
  .cover--two .series-band { left: 116px; width: 516px; top: 942px; font-size: 30px; }
  .cover--three .series-band { left: 66px; width: 604px; top: 968px; }

  .subtitle { position: absolute; left: 24px; right: 0; text-align: center; font-size: 27px; line-height: 30px; }
  .cover--one .subtitle { top: 986px; }
  .cover--two .subtitle { top: 1018px; font-size: 24px; line-height: 28px; left: 0; }

  .sticker {
    position: absolute; left: 78px; top: 120px; width: 208px; height: 208px;
    border-radius: 50%; background: var(--gold); color: var(--ink-violet);
    display: flex; align-items: center; justify-content: center; text-align: center;
    font-size: 19px; font-weight: 700; line-height: 23px;
    transform: rotate(-9deg);
  }
</style>
</head>
<body>

<section class="cover cover--one">
  <svg class="backdrop" viewBox="0 0 720 1150" preserveAspectRatio="none" aria-hidden="true">
    <rect width="720" height="1150" fill="#24163a"/>
    <polygon points="0,0 720,0 720,520 260,0" fill="#2f1f48"/>
    <polygon points="0,480 420,1150 0,1150" fill="#1a0f28"/>
    <polygon points="360,0 720,0 720,300" fill="#3a2858"/>
    <polygon points="0,760 260,1150 0,1150" fill="#150b22"/>
    <line x1="40" y1="0" x2="330" y2="640" stroke="#c99a2e" stroke-width="2.5"/>
    <line x1="0" y1="1150" x2="720" y2="860" stroke="#c99a2e" stroke-width="2"/>
  </svg>
  <div class="portrait" role="img" aria-label="Freigestelltes Foto des Autors im braunen Anzug"></div>
  <p class="author"><strong>ANSELM BERGER –</strong><br><span>Der Wohnwertlotse</span></p>
  <h1 class="title">
    <span class="title__line title__line--gold">BAUE</span>
    <span class="title__line title__line--gold">MAUERN</span>
    <span class="title__joiner">und</span>
    <span class="title__line title__line--white">BLEIBE</span>
    <span class="title__line title__line--white">STILL</span>
  </h1>
  <p class="series-band series-band--gold">GESPRÄCHE ÜBER IMMOBILIEN</p>
  <p class="subtitle">Lassen Sie uns unter Freunden in entspannter<br>Atmosphäre über Immobilien sprechen</p>
</section>

<section class="cover cover--two">
  <svg class="backdrop" viewBox="0 0 720 1150" preserveAspectRatio="none" aria-hidden="true">
    <rect width="720" height="1150" fill="#24163a"/>
    <polygon points="0,0 720,0 720,560 300,0" fill="#2f1f48"/>
    <polygon points="0,520 400,1150 0,1150" fill="#1a0f28"/>
    <polygon points="380,0 720,0 720,320" fill="#3a2858"/>
    <line x1="40" y1="0" x2="310" y2="620" stroke="#c99a2e" stroke-width="2.5"/>
    <line x1="0" y1="1100" x2="720" y2="820" stroke="#c99a2e" stroke-width="2"/>
  </svg>
  <div class="portrait" role="img" aria-label="Freigestelltes Foto des Autors im braunen Anzug"></div>
  <p class="author"><strong>ANSELM BERGER –</strong> <span>DER WOHNWERTLOTSE</span></p>
  <h1 class="title">
    <span class="title__line title__line--gold">BAUE</span>
    <span class="title__line title__line--gold">MAUERN</span>
    <span class="title__joiner">und</span>
    <span class="title__line title__line--white">BLEIBE</span>
    <span class="title__line title__line--white">STILL</span>
  </h1>
  <p class="series-band series-band--violet">GESPRÄCHE ÜBER IMMOBILIEN</p>
  <p class="subtitle">Lassen Sie uns unter Freunden in entspannter<br>Atmosphäre über Immobilien sprechen</p>
</section>

<section class="cover cover--three">
  <svg class="backdrop" viewBox="0 0 720 1150" preserveAspectRatio="none" aria-hidden="true">
    <rect width="720" height="1150" fill="#24163a"/>
    <polygon points="0,0 720,0 720,560 300,0" fill="#2f1f48"/>
    <polygon points="0,520 400,1150 0,1150" fill="#1a0f28"/>
    <polygon points="380,0 720,0 720,320" fill="#3a2858"/>
    <line x1="40" y1="0" x2="310" y2="620" stroke="#c99a2e" stroke-width="2.5"/>
    <line x1="0" y1="1100" x2="720" y2="820" stroke="#c99a2e" stroke-width="2"/>
  </svg>
  <div class="portrait" role="img" aria-label="Freigestelltes Foto des Autors im braunen Anzug"></div>
  <p class="author"><strong>ANSELM BERGER –</strong> <span>DER WOHNWERTLOTSE</span></p>
  <p class="sticker">Lassen Sie<br>uns unter Freunden<br>in entspannter<br>Atmosphäre über<br>Immobilien<br>sprechen</p>
  <h1 class="title">
    <span class="title__line title__line--gold">BAUE</span>
    <span class="title__line title__line--gold">MAUERN</span>
    <span class="title__joiner">und</span>
    <span class="title__line title__line--white">BLEIBE</span>
    <span class="title__line title__line--white">STILL</span>
  </h1>
  <p class="series-band series-band--violet">GESPRÄCHE ÜBER IMMOBILIEN</p>
</section>

</body>
</html>
```